Keystonery Billboard - Financial Services Company (Investments, Tax Planning and Insurance)

Our new office has a billboard directly above the office building. We'd like something eye-catching with a strong Call to Action, with the main part of the billboard being under 7 words if possible. We'd like you to include a way to get ahold of us (either our website keystoneryllc.example or our phone number 302-418-2907. You may also include in small font something to indicate that we've been serving the area since 1980 (the DE area, the tri-state area, the Marlowe Hollow, etc.)

We offer financial planning, tax planning, and insurance, and we help our clients to focus on their goals and happiness by providing everything they need for lifelong wealth under one roof.

Our logos are attached, we use a triangle logo with green and gray. We use the tagline "discover lasting prosperity" but this does not need to be included.

Potential ideas we have seen from other financial companies-
- the concept that the driver spends more time looking at billboards than planning for their retirement
-something along the lines of "everything you need for your finances is in this building right here" planning, investments, taxes, insurance"
-don't spend your time worrying about retirement, let us help you plan for it
-are you working for your money, or is it working for you?
- retirement takes planning, we're here to help
- ready to retire? talk to us
- need investment advice?
- need help investing?
- crossing your fingers isn't a retirement plan. we can help.
- retiring soon? you need help.

Those are just general ideas, please feel free to be creative.

brand colors:
#00b585
#00b185
#000000
#ffffff
#6d6f75
#6d6f75
#6f7074
#021712
#052e24

```html
<!DOCTYPE html>
<html lang="en">
<head>
<meta charset="UTF-8">
<title>Keystonery Billboard</title>
<link href="https://fonts.googleapis.com/css2?family=Poppins:wght@500;800&display=swap" rel="stylesheet">
<style>
  :root {
    --brand-green: #00b585;
    --brand-black: #000000;
    --band-black: #1b1b1b;
    --white: #ffffff;
    --slate: #6d6f75;
    --ink: #333333;
    --photo-deep: #052e24;
    --photo-mid: #3d5a7a;
    --photo-warm: #a69a5c;
    --page: #ffffff;
  }
  * { margin: 0; padding: 0; box-sizing: border-box; }
  html, body {
    width: 835px;
    height: 1200px;
    overflow: hidden;
    background: var(--page);
    font-family: "Poppins", sans-serif;
  }
  .billboard {
    position: absolute;
    left: 30px;
    top: 487px;
    width: 775px;
    height: 225px;
    background: var(--white);
    box-shadow: 0 6px 14px rgba(0, 0, 0, 0.18);
    overflow: hidden;
  }
  .billboard-art {
    position: absolute;
    inset: 0;
  }
  .brand {
    position: absolute;
    left: 124px;
    top: 10px;
    width: 260px;
    display: flex;
    flex-direction: column;
    align-items: center;
  }
  .brand-name {
    font-weight: 800;
    font-size: 36px;
    line-height: 44px;
    color: var(--brand-green);
    letter-spacing: -0.5px;
  }
  .brand-tagline {
    font-weight: 500;
    font-size: 6.5px;
    letter-spacing: 3.2px;
    color: var(--slate);
    text-transform: uppercase;
    margin-top: 1px;
  }
  .headline-band {
    position: absolute;
    left: 0;
    top: 72px;
    width: 500px;
    height: 99px;
    background: var(--band-black);
    text-align: center;
  }
  .headline {
    font-weight: 800;
    font-size: 44px;
    line-height: 46px;
    letter-spacing: -1px;
    color: var(--white);
    margin-top: 4px;
  }
  .call-to-action {
    font-weight: 800;
    font-size: 44px;
    line-height: 44px;
    letter-spacing: -1px;
    color: var(--brand-green);
  }
  .phone {
    position: absolute;
    left: 40px;
    top: 176px;
    display: flex;
    align-items: center;
    gap: 12px;
  }
  .phone-icon { width: 30px; height: 30px; }
  .phone-number {
    font-weight: 800;
    font-size: 45px;
    line-height: 45px;
    letter-spacing: -0.5px;
    color: var(--ink);
  }
</style>
</head>
<body>
  <div class="billboard">
    <svg class="billboard-art" width="775" height="225" viewBox="0 0 775 225">
      <defs>
        <linearGradient id="photo-tone" x1="0" y1="0" x2="1" y2="1">
          <stop offset="0" stop-color="var(--photo-deep)"/>
          <stop offset="0.45" stop-color="var(--photo-mid)"/>
          <stop offset="1" stop-color="var(--photo-warm)"/>
        </linearGradient>
      </defs>
      <path class="accent-arc" d="M528 33 Q482 120 562 225 L578 225 Q500 130 533 36 Z" fill="var(--brand-green)"/>
      <path class="photo-area" role="img" aria-label="Photo of a joyful retired couple riding a scooter together on a leafy city street"
            d="M560 0 Q505 110 575 225 L775 225 L775 0 Z" fill="url(#photo-tone)"/>
    </svg>

    <div class="brand">
      <div class="brand-name">Keystonery</div>
      <div class="brand-tagline">Discover lasting prosperity</div>
    </div>

    <div class="headline-band">
      <div class="headline">READY TO RETIRE?</div>
      <div class="call-to-action">TALK TO US</div>
    </div>

    <div class="phone">
      <svg class="phone-icon" viewBox="0 0 24 24" aria-hidden="true">
        <path d="M6.6 10.8a15.1 15.1 0 0 0 6.6 6.6l2.2-2.2a1 1 0 0 1 1-.25 11.4 11.4 0 0 0 3.6.57 1 1 0 0 1 1 1V20a1 1 0 0 1-1 1A17 17 0 0 1 3 4a1 1 0 0 1 1-1h3.5a1 1 0 0 1 1 1c0 1.25.2 2.45.57 3.57a1 1 0 0 1-.25 1z" fill="var(--brand-green)"/>
        <path d="M14 3.2a7.5 7.5 0 0 1 6.8 6.8M14 6.4a4.3 4.3 0 0 1 3.6 3.6" fill="none" stroke="var(--brand-green)" stroke-width="1.8" stroke-linecap="round"/>
      </svg>
      <span class="phone-number">302-418-2907</span>
    </div>
  </div>
</body>
</html>
```